Full Business Set-Up Stationary, Folder, Envelope, & Business Card, etc. CPA Firm
CPA Firm Collarteral Package
Full Business Set-Up Stationary, Folder, Envelope, & Business Card, etc. CPA Firm - Consulting
Creative Brief
Bright & Fun-filled
Mara Benton, CPA
Certified Public Accountant
512 Wexford Lane Suite 200 Brandon, FL 33571
MaraBenton@ledgerwisemail.com
www.MaraBentonCPA-example.com
AC58163
Key Words: CPA since 1999 Servicing State of Florida since 1999 Certified Management Accountant Certified Public Accounting Firm Award Winning CPA Award Winning Professional Officies Located in the Hillcrest Merchants Guild Building Trustworthy, Professional, Experienced
Tag Line: See the Clear Path Steadfast Services
marabenton marabenton
Thanks for your submissions. Please include portfolio for the Firm. Particularly a Business Folder and Letterhead/Envelope. Ipad and Iphone Designs.

```html
<!DOCTYPE html>
<html lang="en">
<head>
<meta charset="utf-8">
<title>Mara Benton CPA – Business Card</title>
<link rel="stylesheet" href="https://fonts.googleapis.com/css2?family=Cinzel:wght@400;600&family=Cormorant+Garamond:wght@500;600&display=swap">
<style>
  :root{
    --bg:#8e8f91;
    --blue:#2a7fd4;
    --blue-deep:#1a5fb3;
    --blue-text:#2b6fc2;
    --green:#8cc63f;
    --grey-text:#8a8f96;
    --ink:#3a4a5c;
    --white:#ffffff;
  }
  *{box-sizing:border-box;margin:0;padding:0}
  html,body{width:1200px;height:908px;overflow:hidden}
  body{background:var(--bg);position:relative;font-family:"Cormorant Garamond",serif}
  .card{position:absolute;width:525px;height:300px;border-radius:22px;overflow:hidden;box-shadow:0 14px 30px rgba(0,0,0,.28)}
  .card--front{left:70px;top:140px;background:linear-gradient(135deg,var(--blue) 0%,var(--blue-deep) 100%)}
  .card--back{left:605px;top:460px;background:var(--white)}
  .front__mark{position:absolute;right:60px;top:40px;width:190px;height:190px;border-radius:50%;background:rgba(255,255,255,.12)}
  .front__name{position:absolute;left:40px;top:118px;font-family:"Cinzel",serif;font-weight:400;font-size:30px;color:var(--white);letter-spacing:.5px}
  .front__tagline{position:absolute;left:42px;top:160px;font-family:"Cinzel",serif;font-size:11px;color:var(--white);letter-spacing:5px}
  .back__swoosh{position:absolute;inset:0;width:100%;height:100%}
  .back__logo{position:absolute;left:50px;top:80px;display:flex;align-items:center;gap:10px}
  .back__logo-dot{width:26px;height:26px;border-radius:50%;background:var(--green)}
  .back__logo-name{font-family:"Cinzel",serif;font-weight:600;font-size:15px;color:var(--blue-text)}
  .back__tagline{position:absolute;left:50px;top:116px;font-family:"Cinzel",serif;font-size:8px;letter-spacing:3px;color:var(--grey-text)}
  .back__name{position:absolute;left:50px;top:168px;font-family:"Cinzel",serif;font-size:22px;color:var(--blue-text)}
  .back__title{position:absolute;left:52px;top:200px;font-family:"Cinzel",serif;font-size:10px;letter-spacing:1.5px;color:var(--grey-text)}
  .back__contact{position:absolute;left:290px;top:78px;list-style:none;font-size:12px;line-height:17px;color:var(--ink)}
  .back__contact .license{color:var(--blue-text);font-weight:600}
  .back__contact li.icon{display:flex;align-items:center;gap:6px}
  .back__contact svg{flex:none}
</style>
</head>
<body>
  <section class="card card--front">
    <div class="front__mark" role="img" aria-label="Faint brand emblem"></div>
    <h1 class="front__name">Mara Benton CPA</h1>
    <p class="front__tagline">SEE THE CLEAR PATH</p>
  </section>

  <section class="card card--back">
    <svg class="back__swoosh" viewBox="0 0 525 300" preserveAspectRatio="none" aria-hidden="true">
      <path d="M300 0 Q470 10 525 95 L525 0 Z" fill="var(--blue)"/>
      <path d="M290 0 Q470 18 525 105" fill="none" stroke="var(--green)" stroke-width="4"/>
      <path d="M0 225 Q120 290 300 300 L0 300 Z" fill="var(--blue)"/>
      <path d="M0 212 Q130 285 320 300" fill="none" stroke="var(--green)" stroke-width="4"/>
    </svg>
    <div class="back__logo">
      <span class="back__logo-dot"></span>
      <span class="back__logo-name">Mara Benton CPA</span>
    </div>
    <p class="back__tagline">SEE THE CLEAR PATH</p>
    <h2 class="back__name">Mara Benton CPA</h2>
    <p class="back__title">CERTIFIED PUBLIC ACCOUNTANT</p>
    <ul class="back__contact">
      <li class="license">License No. AC58163</li>
      <li>512 Wexford Lane Suite 200</li>
      <li>Brandon, FL 33571</li>
      <li class="icon"><svg width="9" height="9"><circle cx="4.5" cy="4.5" r="4.5" fill="var(--green)"/></svg>813.555.0142</li>
      <li class="icon"><svg width="9" height="9"><circle cx="4.5" cy="4.5" r="4.5" fill="var(--green)"/></svg>813.555.0187</li>
      <li class="icon"><svg width="9" height="9"><circle cx="4.5" cy="4.5" r="4.5" fill="var(--green)"/></svg>MaraBenton@ledgerwisemail.com</li>
      <li class="icon"><svg width="9" height="9"><circle cx="4.5" cy="4.5" r="4.5" fill="var(--green)"/></svg>www.MaraBentonCPA-example.com</li>
    </ul>
  </section>
</body>
</html>
```